Small environmental consultancy needs a simple but professional web design

We are a boutique environmental consultancyand contracting business located in Margaret River in the South West of Western Australia.

We have two arms
1) Consulting which offers environmental planning, management and assessment services primarily to local government and the development industry.
2) Contracting which implements on site plans and on ground works primarily involving revegetation, bush regeneration and environmental weed control.

We need a simple yet professional web design within the wordpress platform that commmunicates professionalism, experience and technical expertise without appearing too corporate.

Something like this structure appeals:
http://fernquill.net.au/environment-services/
or
http://www.tallowbrookenvironmental.com.au/index.php

(without the image gallery function)

Target Market(s)

Local Government Officers deciding on tenders;
Developers, Engineers, Town Planning consultants looking for environmental expertise

Industry/Entity Type

Business

Number of Pages Required

5+ page

Font styles to use
Sans Serif

Colors
33a6d7
9bcb3c

Requirements
Must have
• Pages required include:
• Home
• Environmental Planning and Management
• Revegetation and Regeneration Implementation (This page can mirror the Environmental Planning and Management page exactly in structure but with different text and images)
• About Us (I think that this page can be relatively simple and generic)
• Contact (I think that this page can be very simple and generic)
Nice to have
• An ability to start out basic and quicikly establish a website presence and then build in additional drop downs and pages over time.
Should not have
• It does not need a photo gallery page;
• It does not need a major amount of space dedicated to social media and blogs etc as this is not currently particularly active area for us

```html
<!DOCTYPE html>
<html lang="en">
<head>
<meta charset="utf-8">
<title>Myrtleby Ecoservices</title>
<link href="https://fonts.googleapis.com/css2?family=Oswald:wght@400;500;700&family=Open+Sans:wght@400;600;700&family=Dancing+Script:wght@700&display=swap" rel="stylesheet">
<style>
:root{
  --blue:#33a6d7;
  --blue-dark:#1f86b8;
  --green:#9bcb3c;
  --green-dark:#6fa51e;
  --text:#6b6b6b;
  --heading:#3b3b3b;
  --light:#f1f1f1;
  --footer:#e6e6e6;
  --white:#ffffff;
}
*{box-sizing:border-box;margin:0;padding:0}
html,body{width:1200px;height:2688px;overflow:hidden}
body{background:var(--white);font-family:"Open Sans",Arial,sans-serif;color:var(--text);position:relative}
.page{position:relative;width:1200px;height:2688px}

/* header */
.site-header{position:absolute;left:0;top:0;width:1200px;height:176px}
.brand{position:absolute;left:60px;top:36px;display:flex;align-items:center;gap:18px}
.brand-mark{width:64px;height:64px;border-radius:50%;background:var(--green)}
.brand-name{font-family:"Oswald",sans-serif;font-weight:500;font-size:40px;color:var(--blue-dark);line-height:1}
.brand-tag{font-size:15px;color:var(--green-dark);margin-top:6px;font-weight:600}
.call{position:absolute;right:64px;top:34px;text-align:right}
.call-label{font-family:"Oswald",sans-serif;font-size:22px;color:var(--heading)}
.call-number{font-family:"Oswald",sans-serif;font-weight:700;font-size:38px;color:var(--blue);line-height:1.1}
.search{position:absolute;right:64px;top:112px;width:240px;height:40px;border:2px solid #d6d6d6;border-radius:4px;font-size:15px;color:#aaa;padding:8px 12px}
.search svg{position:absolute;right:10px;top:9px}
.main-nav{position:absolute;left:0;top:176px;width:1200px;height:46px;background:var(--blue);display:flex;justify-content:space-between;padding:0 40px}
.main-nav a{font-family:"Oswald",sans-serif;font-size:15px;color:var(--white);text-decoration:none;padding:0 22px;line-height:46px;letter-spacing:.4px;white-space:nowrap}
.main-nav a.current{background:var(--blue-dark)}

/* hero */
.hero{position:absolute;left:0;top:222px;width:1200px;height:440px;background:linear-gradient(180deg,#c9d9cc 0%,#8fae7c 45%,#4d6b3a 100%)}
.hero-arrow{position:absolute;top:190px;width:48px;height:48px;border-radius:50%;background:rgba(40,40,40,.7)}
.hero-arrow.prev{left:20px}.hero-arrow.next{right:20px}
.hero-arrow svg{position:absolute;left:14px;top:14px}

/* features */
.feature-badges{position:absolute;left:0;top:560px;width:1200px;height:340px}
.badge{position:absolute;top:0;width:300px;height:300px;border:8px solid var(--blue);border-radius:50%;border-top-left-radius:0;transform:rotate(45deg)}
.badge.b1{left:120px;background:linear-gradient(135deg,#3f7d2a,#c8392a 60%,#2f6a1f)}
.badge.b2{left:450px;background:linear-gradient(135deg,#5a8f3a,#d94432 55%,#6b9b3e)}
.badge.b3{left:780px;background:linear-gradient(135deg,#3b6e2c,#d6442f 55%,#7aa24a)}
.features{position:absolute;left:100px;top:920px;width:1000px;display:flex;justify-content:space-between}
.feature{width:300px}
.feature h2{font-family:"Oswald",sans-serif;font-weight:700;font-size:30px;color:var(--green-dark);text-transform:uppercase;margin-bottom:14px}
.feature p{font-size:15px;line-height:23px}
.btn-more{display:inline-block;margin-top:20px;background:var(--blue);color:var(--white);font-size:12px;font-weight:700;padding:6px 16px;border-radius:3px;text-transform:uppercase}

/* welcome */
.welcome{position:absolute;left:0;top:1170px;width:1200px;height:500px;background:linear-gradient(90deg,#fff 45%,#eef6ea 75%,#e3f0f6 100%)}
.welcome-visual{position:absolute;right:60px;top:60px;width:380px;height:380px;border-radius:50%;background:radial-gradient(circle at 40% 40%,#d9eefa,#a9d4ea 55%,#cfe6c3 100%);opacity:.75}
.welcome-text{position:absolute;left:100px;top:20px;width:760px}
.welcome-script{font-family:"Dancing Script",cursive;font-size:46px;color:var(--green)}
.welcome-title{font-family:"Oswald",sans-serif;font-weight:700;font-size:60px;color:var(--green);line-height:1;margin:-6px 0 24px}
.welcome-text p{font-size:15px;line-height:23px;margin-bottom:18px}

/* testimonials + why */
.section-title{font-family:"Oswald",sans-serif;font-weight:500;font-size:26px;color:var(--heading);text-transform:uppercase}
.testimonials{position:absolute;left:100px;top:1730px;width:500px}
.quote{background:var(--light);padding:26px 30px;margin-top:26px;font-size:14px;line-height:22px;font-style:italic;position:relative}
.quote cite{display:block;margin-top:12px;font-style:normal;font-weight:700;color:var(--heading)}
.stars{display:flex;gap:4px;margin-top:6px}
.why{position:absolute;left:680px;top:1730px;width:420px}
.why-item{position:relative;margin-top:38px;height:150px}
.why-icon{position:absolute;left:0;top:24px;width:96px;height:96px;border-radius:50%;background:var(--blue);border:6px solid #d4ecf7}
.why-icon svg{position:absolute;left:22px;top:22px}
.why-box{position:absolute;left:60px;top:0;width:360px;height:150px;border:2px solid var(--blue);padding:20px 20px 0 60px;background:var(--white)}
.why-box h3{font-family:"Oswald",sans-serif;font-weight:500;font-size:17px;color:var(--blue-dark);margin-bottom:8px;white-space:nowrap}
.why-box p{font-size:13px;line-height:20px}

/* footer */
.site-footer{position:absolute;left:0;top:2380px;width:1200px;height:262px;background:var(--footer)}
.footer-col{position:absolute;top:24px}
.footer-col h4{font-family:"Oswald",sans-serif;font-weight:500;font-size:17px;color:var(--heading);text-transform:uppercase;margin-bottom:8px}
.footer-col li{list-style:none;font-size:13px;line-height:21px}
.footer-phone{font-family:"Oswald",sans-serif;font-weight:700;font-size:26px;color:var(--blue)}
.contact-form{position:absolute;left:610px;top:24px;width:490px}
.contact-form .section-title{font-size:17px;margin-bottom:10px}
.form-fields{display:flex;flex-wrap:wrap;gap:10px}
.field{display:block;width:240px;height:36px;background:var(--white);border:1px solid #d0d0d0;font-size:13px;color:#aaa;padding:8px 12px}
.field.wide{width:490px;height:70px}
.btn-send{display:inline-block;margin-top:12px;background:var(--green);color:var(--white);font-family:"Oswald",sans-serif;font-size:16px;padding:8px 22px;text-transform:uppercase}
.copyright{position:absolute;left:0;top:2642px;width:1200px;height:46px;background:#d6d6d6;font-size:13px;line-height:46px;padding-left:100px}
</style>
</head>
<body>
<div class="page">

<header class="site-header">
  <div class="brand">
    <div class="brand-mark"></div>
    <div>
      <div class="brand-name">Myrtleby Ecoservices</div>
      <div class="brand-tag">Environmental Services, Planning &amp; Management</div>
    </div>
  </div>
  <div class="call">
    <div class="call-label">Call Us</div>
    <div class="call-number">0412 638 104</div>
  </div>
  <div class="search">Search
    <svg width="20" height="20" viewBox="0 0 20 20"><circle cx="8" cy="8" r="6" fill="none" stroke="#33a6d7" stroke-width="2.5"/><line x1="12.5" y1="12.5" x2="18" y2="18" stroke="#33a6d7" stroke-width="2.5"/></svg>
  </div>
</header>

<nav class="main-nav">
  <a class="current">HOME</a>
  <a>ENVIRONMENTAL PLANNING AND MANAGEMENT</a>
  <a>REVEGETATION AND REGENERATION IMPLEMENTATION</a>
  <a>ABOUT US</a>
  <a>CONTACT</a>
</nav>

<section class="hero" role="img" aria-label="Sunlit forest with tall trees and morning mist">
  <div class="hero-arrow prev"><svg width="20" height="20" viewBox="0 0 20 20"><path d="M13 3 L6 10 L13 17" fill="none" stroke="#fff" stroke-width="3"/></svg></div>
  <div class="hero-arrow next"><svg width="20" height="20" viewBox="0 0 20 20"><path d="M7 3 L14 10 L7 17" fill="none" stroke="#fff" stroke-width="3"/></svg></div>
</section>

<div class="feature-badges">
  <div class="badge b1" role="img" aria-label="Red native flowers among green leaves"></div>
  <div class="badge b2" role="img" aria-label="Close-up of red flowering shrub"></div>
  <div class="badge b3" role="img" aria-label="Red blossoms in bushland"></div>
</div>

<section class="features">
  <div class="feature">
    <h2>About Us</h2>
    <p>A boutique consultancy in Margaret River offering planning, assessment and on-ground works across the South West.</p>
    <span class="btn-more">Read more</span>
  </div>
  <div class="feature">
    <h2>Why Us?</h2>
    <p>Local experience, technical expertise and practical field crews who deliver every plan from desk to site.</p>
    <span class="btn-more">Read more</span>
  </div>
  <div class="feature">
    <h2>Current Project</h2>
    <p>Revegetation of a coastal reserve with local seedlings and staged weed control over three seasons.</p>
    <span class="btn-more">Read more</span>
  </div>
</section>

<section class="welcome">
  <div class="welcome-visual" role="img" aria-label="Hands holding a green globe"></div>
  <div class="welcome-text">
    <div class="welcome-script">Welcome to</div>
    <div class="welcome-title">MYRTLEBY ECOSERVICES</div>
    <p>We provide environmental planning, management and assessment services to local government and the development industry, helping projects meet their approvals with clear and sound advice.</p>
    <p>Our contracting arm puts plans into action on the ground. Our crews carry out revegetation, bush regeneration and environmental weed control, working with care for each site and the species that depend on it.</p>
    <p>Based in the South West of Western Australia, we combine local knowledge with technical skill and a friendly, practical approach to every job we take on.</p>
    <span class="btn-more">Read more</span>
  </div>
</section>

<section class="testimonials">
  <h2 class="section-title">Client's Testimonials</h2>
  <div class="quote">"Their team gave clear advice on our subdivision and managed the approvals process smoothly. Reports were thorough and delivered on time, and the site works were carried out with real care."
    <cite>- Mark Dalton</cite>
    <div class="stars">
      <svg width="22" height="22" viewBox="0 0 24 24"><path d="M12 2l3 7 7 .6-5.3 4.7 1.6 7.2L12 17.8 5.7 21.5l1.6-7.2L2 9.6 9 9z" fill="#f2b632"/></svg>
      <svg width="22" height="22" viewBox="0 0 24 24"><path d="M12 2l3 7 7 .6-5.3 4.7 1.6 7.2L12 17.8 5.7 21.5l1.6-7.2L2 9.6 9 9z" fill="#f2b632"/></svg>
      <svg width="22" height="22" viewBox="0 0 24 24"><path d="M12 2l3 7 7 .6-5.3 4.7 1.6 7.2L12 17.8 5.7 21.5l1.6-7.2L2 9.6 9 9z" fill="#f2b632"/></svg>
      <svg width="22" height="22" viewBox="0 0 24 24"><path d="M12 2l3 7 7 .6-5.3 4.7 1.6 7.2L12 17.8 5.7 21.5l1.6-7.2L2 9.6 9 9z" fill="#f2b632"/></svg>
      <svg width="22" height="22" viewBox="0 0 24 24"><path d="M12 2l3 7 7 .6-5.3 4.7 1.6 7.2L12 17.8 5.7 21.5l1.6-7.2L2 9.6 9 9z" fill="#cfcfcf"/></svg>
    </div>
  </div>
  <div class="quote">"We engaged them for a bush regeneration program on our reserve. The crew were professional, knowledgeable and easy to work with, and the results speak for themselves."
    <cite>- Ruth Avery</cite>
    <div class="stars">
      <svg width="22" height="22" viewBox="0 0 24 24"><path d="M12 2l3 7 7 .6-5.3 4.7 1.6 7.2L12 17.8 5.7 21.5l1.6-7.2L2 9.6 9 9z" fill="#f2b632"/></svg>
      <svg width="22" height="22" viewBox="0 0 24 24"><path d="M12 2l3 7 7 .6-5.3 4.7 1.6 7.2L12 17.8 5.7 21.5l1.6-7.2L2 9.6 9 9z" fill="#f2b632"/></svg>
      <svg width="22" height="22" viewBox="0 0 24 24"><path d="M12 2l3 7 7 .6-5.3 4.7 1.6 7.2L12 17.8 5.7 21.5l1.6-7.2L2 9.6 9 9z" fill="#f2b632"/></svg>
      <svg width="22" height="22" viewBox="0 0 24 24"><path d="M12 2l3 7 7 .6-5.3 4.7 1.6 7.2L12 17.8 5.7 21.5l1.6-7.2L2 9.6 9 9z" fill="#cfcfcf"/></svg>
      <svg width="22" height="22" viewBox="0 0 24 24"><path d="M12 2l3 7 7 .6-5.3 4.7 1.6 7.2L12 17.8 5.7 21.5l1.6-7.2L2 9.6 9 9z" fill="#cfcfcf"/></svg>
    </div>
  </div>
</section>

<section class="why">
  <h2 class="section-title">Why Us?</h2>
  <div class="why-item">
    <div class="why-box"><h3>LOCAL KNOWLEDGE OF THE REGION</h3><p>Years of field work across the South West give us a strong grasp of local species, soils and planning rules.</p></div>
    <div class="why-icon"><svg width="40" height="40" viewBox="0 0 40 40"><path d="M20 4 C32 8 34 22 20 36 C6 22 8 8 20 4Z" fill="#fff"/></svg></div>
  </div>
  <div class="why-item">
    <div class="why-box"><h3>TECHNICAL EXPERTISE YOU CAN TRUST</h3><p>Qualified consultants prepare clear, defensible reports for councils, developers and planners.</p></div>
    <div class="why-icon"><svg width="40" height="40" viewBox="0 0 40 40"><path d="M8 21 L17 30 L33 11" fill="none" stroke="#fff" stroke-width="5"/></svg></div>
  </div>
  <div class="why-item">
    <div class="why-box"><h3>FROM PLAN TO ON-GROUND WORKS</h3><p>One team handles both the planning and the revegetation works, keeping every project simple and joined up.</p></div>
    <div class="why-icon"><svg width="40" height="40" viewBox="0 0 40 40"><path d="M6 20 H30 M22 11 L31 20 L22 29" fill="none" stroke="#fff" stroke-width="5"/></svg></div>
  </div>
</section>

<footer class="site-footer">
  <div class="footer-col" style="left:100px">
    <h4>About</h4>
    <ul><li>Environmental Planning and Management</li><li>Revegetation and Bush Regeneration</li><li>Contacts</li></ul>
    <h4 style="margin-top:16px">Call Us Now</h4>
    <div class="footer-phone">+61 8 9757 0420</div>
  </div>
  <div class="footer-col" style="left:380px">
    <h4>Legal</h4>
    <ul><li>Terms of Service</li><li>Privacy Policy</li><li>Cookie Policy</li></ul>
    <h4 style="margin-top:16px">Website</h4>
    <ul><li>www.myrtlebyecoservices.com.au</li></ul>
  </div>
  <div class="contact-form">
    <h4 class="section-title">Contact Us</h4>
    <div class="form-fields">
      <span class="field">Name</span>
      <span class="field">E-mail</span>
      <span class="field wide">Message</span>
    </div>
    <span class="btn-send">Send Message</span>
  </div>
</footer>
<div class="copyright">© 2015 Myrtleby Ecoservices. All Rights Reserved.</div>

</div>
</body>
</html>
```